MBRDC redesign and update stationary bc envelopes.

Stationary, Envelopes, Brochures, Business Card. Need to add second surgeon and two other offices. I need everything to match. I am a oral & maxillofacial surgeon.
Additional surgeon and three office addresses.
Jae Min Park, DMD, MD, INC

3718 Silver Meadow Parkway
Cedar Ridge, CA 95710

642 Lorin Way, Suite 101
Brookvale, CA. 95622

2317 Vale Street, Suite 105
Pine Hollow, CA. 95614
Updates

Logo design uploaded. Zapfino Extra/Adobe Garamond/Palatino are fonts used before. Not sure what is on exisiting stationary.

Target Market(s)

Referral dentist and sometimes patients. I am a oral & Maxillofacial surgeon.

Industry/Entity Type

Dental Clinic

Font styles to use
Serif
Script

Requirements
Must have
• Color of existing stationary. Update is possible.
Nice to have
• Conservative/modern
Should not have
• Playful

```html
<!DOCTYPE html>
<html lang="en">
<head>
<meta charset="utf-8">
<title>MBRDC Business Card</title>
<link rel="stylesheet" href="https://fonts.googleapis.com/css2?family=EB+Garamond:wght@500;600&family=PT+Serif&family=Roboto:wght@400&display=swap">
<style>
:root{
  --bg:#8f8f8f;
  --card:#ffffff;
  --brown:#5a4236;
  --band:#6b4f40;
  --green:#5f8a1f;
  --seal:#e6ecd6;
  --mark:#dfe9c8;
}
*{margin:0;padding:0;box-sizing:border-box}
html,body{width:1188px;height:1200px;overflow:hidden;background:var(--bg)}
.card{position:absolute;left:245px;width:696px;height:386px;background:var(--card);overflow:hidden;color:var(--brown);font-family:"PT Serif",Georgia,serif}
.card--front{top:159px}
.card--back{top:627px}
.surgeon-name{position:absolute;left:38px;top:60px;font-family:"EB Garamond",Georgia,serif;font-weight:600;font-size:25px;white-space:nowrap}
.board-seal{position:absolute;left:37px;top:96px;width:37px;height:37px;border-radius:50%;background:var(--seal);border:1.5px solid var(--green)}
.board-credential{position:absolute;left:81px;top:93px;font-family:"Roboto",Arial,sans-serif;font-size:15px;line-height:19px;color:var(--green)}
.main-address{position:absolute;left:38px;top:155px;font-size:17px;line-height:21px}
.contact-list{position:absolute;left:38px;top:205px;list-style:none;font-size:17px;line-height:22px}
.contact-list li{display:flex;align-items:center;gap:6px;height:22px}
.contact-list svg{width:15px;height:15px;flex:none}
.practice-mark{position:absolute;left:413px;top:26px;width:245px;text-align:center}
.practice-mark .mark-circle{display:block;width:92px;height:92px;border-radius:50%;background:var(--mark);margin:0 auto 8px}
.practice-name{font-family:"EB Garamond",Georgia,serif;font-weight:500;color:var(--brown)}
.practice-name .name-main{display:block;font-size:27px;line-height:28px}
.practice-name .name-sub{display:block;font-size:17px;line-height:20px}
.branch-offices{position:absolute;right:38px;top:202px;text-align:right;font-size:17px;line-height:21px}
.branch-offices p+p{margin-top:6px}
.services{position:absolute;left:0;right:0;top:299px;text-align:center;font-size:17px;line-height:23px}
.services .dot{color:var(--green);font-size:12px;margin:0 3px 0 6px;vertical-align:1px}
.card--back .practice-mark{left:0;right:0;top:72px;width:auto}
.card--back .mark-circle{width:122px;height:122px;margin-bottom:12px}
.card--back .name-main{font-size:40px;line-height:42px}
.card--back .name-sub{font-size:26px;line-height:30px}
.web-band{position:absolute;left:0;right:0;bottom:0;height:42px;background:var(--band);color:#fff;font-size:21px;line-height:42px;text-align:center}
</style>
</head>
<body>
<section class="card card--front">
  <h1 class="surgeon-name">Jae Min Park, DMD, MD, INC</h1>
  <span class="board-seal" aria-hidden="true"></span>
  <p class="board-credential">Diplomate of the Western Board of<br>Oral &amp; Facial Surgeons</p>
  <p class="main-address">3718 Silver Meadow Parkway<br>Cedar Ridge, CA 95710</p>
  <ul class="contact-list">
    <li><svg viewBox="0 0 16 16" aria-label="Phone"><path fill="#5f8a1f" d="M2 5c0-2 3-3 6-3s6 1 6 3v1h-3V5H5v1H2zM4 7h8l2 6H2z"/></svg>916.555.0142</li>
    <li><svg viewBox="0 0 16 16" aria-label="Fax"><path fill="#5f8a1f" d="M4 1h8v4H4zM1 6h14v6h-3v3H4v-3H1zM5 10v4h6v-4z"/></svg>&nbsp;916.555.0187</li>
    <li><svg viewBox="0 0 16 16" aria-label="Email"><rect x="1" y="3" width="14" height="10" fill="#5f8a1f"/><path d="M1.5 3.5 8 9l6.5-5.5" stroke="#fff" stroke-width="1.3" fill="none"/></svg>drpark@silvermeadowsurgery.com</li>
    <li><svg viewBox="0 0 16 16" aria-label="Website"><circle cx="8" cy="8" r="7" fill="#5f8a1f"/><path d="M5 4c2 1 1 3 3 3s1 3 0 4M10 3c1 2 3 2 3 4" stroke="#fff" stroke-width="1.3" fill="none"/></svg>www.silvermeadowsurgery.com</li>
  </ul>
  <div class="practice-mark">
    <span class="mark-circle" aria-hidden="true"></span>
    <p class="practice-name"><span class="name-main">Silver Meadow</span><span class="name-sub">Oral &amp; Facial Surgery Center</span></p>
  </div>
  <div class="branch-offices">
    <p>2317 Vale Street, Suite 105<br>Pine Hollow, CA. 95614</p>
    <p>642 Lorin Way, Suite 101<br>Brookvale, CA. 95622</p>
  </div>
  <p class="services">
    <span class="dot">●</span>Dentoalveolar Surgery <span class="dot">●</span>Dental Implant Surgery <span class="dot">●</span>Orthognathic Surgery<br>
    <span class="dot">●</span>Facial Trauma Surgery <span class="dot">●</span>Preprosthetic and Reconstructive Surgery<br>
    <span class="dot">●</span>TMJ Disorders and Surgery <span class="dot">●</span>Obstructive Sleep Apnea Surgery
  </p>
</section>
<section class="card card--back">
  <div class="practice-mark">
    <span class="mark-circle" aria-hidden="true"></span>
    <p class="practice-name"><span class="name-main">Silver Meadow</span><span class="name-sub">Oral &amp; Facial Surgery Center</span></p>
  </div>
  <p class="web-band">www.silvermeadowsurgery.com</p>
</section>
</body>
</html>
```